BrimLO (Beer/Wine candles) Edgy Candle with a Cause

Help us to help others. BrimLo is a beautifully scented natural soy candle made using repurposed beer/ wine bottles while at the same time donating a portion of our profits to youth alcohol education programs. (1. Waste = Repurposed beer/wine bottle, 2.) BrimLo = (anti) drunk/alcohol 3.) Ed = education/prevention programs.)
We're looking for a design that is cool and bold yet elegant and appeals to women (90% of our customers.) No traditional beer label designs please.

The "BrimLO" logo should appear prominently in the design with the scent name (in a different font) "on top." (See the "Velvet Brimmed" poster attached.

Examples of actual scents: Amber Drift, Glowing Paloma, Fizzing Mock-ree. (None of the fragrances smell like beer/alcohol or wine.)

Also the ED in BrimeLO should stand out in some way.

The emphasis should not be on the recycling aspect, so no obvious recycling symbols.

We are open to different interpretations and have attached varying examples that we like.
Note: a "blackboard/chalkboard" label is an idea since this deals with education.

Note: files & fonts used in the final design should be editable so that we can add other scent names as needed.

Target Market(s)

Candle buyers, specifically women between the ages of 16-45

Requirements
Must have
• 1.)Free fonts or license fonts under $20.00 2.) fonts modified to look unique/original. 3.) Editable Scent name 4.) Burning instructions 5.) Warning Info
• Burning Instructions: Trim wick to 1/4" before each lighting. Keep free from foreign materials including wick trimmings. For an even burn, burn for at least 1 hour but not more than 4 hours at a time. Discontinue use when 1/4" of wax remains. Discard or recycle after use.
• Warning: Burn candle within sight. Keep out of reach of children and pets. Keep away from things that catch fire. Use with caution.
Nice to have
• Colored Scent Names
Should not have
• recycle symbols

```html
<!DOCTYPE html>
<html lang="en">
<head>
<meta charset="utf-8">
<title>BrimLo Beer Bottle Candles – Fizzing Mock-ree</title>
<link rel="stylesheet" href="https://fonts.googleapis.com/css2?family=Cabin+Sketch:wght@700&family=Shadows+Into+Light+Two&family=Sue+Ellen+Francisco&family=Gochi+Hand&display=swap">
<style>
  :root {
    --board-dark: #1c1e1f;
    --board-mid: #2e3131;
    --chalk: #e9e6d8;
    --chalk-soft: #c9c7bd;
    --chalk-grey: #a8a8a4;
    --lime: #a6e23b;
    --coral: #f0574f;
    --amber: #e8a623;
    --hand: "Shadows Into Light Two", cursive;
    --script: "Sue Ellen Francisco", cursive;
    --sketch: "Cabin Sketch", cursive;
  }
  * { margin: 0; padding: 0; box-sizing: border-box; }
  html, body { width: 1200px; height: 933px; overflow: hidden; background: var(--board-dark); }
  .label {
    position: relative; width: 1200px; height: 933px; overflow: hidden;
    background: radial-gradient(ellipse at 45% 40%, var(--board-mid) 0%, #262828 55%, var(--board-dark) 100%);
    color: var(--chalk); font-family: var(--hand);
  }
  .abs { position: absolute; }
  .warning { left: 22px; top: 14px; width: 262px; font-size: 23px; line-height: 25px; font-style: italic; }
  .guide-arrow { left: 284px; top: 138px; }
  .scent-name {
    left: 362px; top: 58px; font-family: var(--script); font-size: 96px; line-height: 1;
    color: var(--lime); transform: rotate(-3deg); transform-origin: left top; white-space: nowrap; letter-spacing: 2px;
  }
  .scent-underline { left: 350px; top: 195px; }
  .ingredients { left: 858px; top: 38px; font-size: 28px; line-height: 43px; }
  .ingredients h2 { font-weight: 400; font-size: 28px; margin-left: 48px; line-height: 46px; }
  .ingredients ul { list-style: none; }
  .ingredients li { display: flex; align-items: center; gap: 4px; }
  .ingredients li svg { flex: none; }
  .discard-note { left: 80px; top: 300px; width: 70px; text-align: center; font-family: "Gochi Hand", cursive; color: var(--amber); font-size: 17px; line-height: 24px; }
  .art { background: linear-gradient(160deg, #4a4c4a, #3a3c3b); border-radius: 6px; opacity: .8; }
  .art-discard { left: 160px; top: 268px; width: 100px; height: 128px; }
  .art-school { left: 1025px; top: 485px; width: 75px; height: 100px; }
  .art-bottles { left: 968px; top: 788px; width: 36px; height: 40px; background: linear-gradient(160deg, #c9a560, #9d9a8f); }
  .brand-name {
    left: 262px; top: 232px; font-family: var(--hand); font-weight: 400; line-height: 1;
    color: var(--coral); white-space: nowrap; letter-spacing: -2px;
  }
  .brand-name .brand-lead { font-size: 215px; }
  .brand-name .brand-ed { font-size: 290px; }
  .cause { left: 900px; top: 333px; width: 285px; font-size: 29px; line-height: 38px; font-style: italic; }
  .cause .mark { text-decoration: underline; text-decoration-color: var(--amber); text-decoration-thickness: 3px; text-underline-offset: 4px; }
  .product-type { left: 314px; top: 597px; font-family: var(--sketch); font-weight: 700; font-size: 46px; color: var(--chalk-grey); white-space: nowrap; }
  .instructions-frame { left: 30px; top: 400px; }
  .instructions {
    left: 56px; top: 424px; height: 470px; width: 200px;
    writing-mode: vertical-rl; transform: rotate(180deg);
    font-size: 22px; line-height: 27px; font-style: italic; color: var(--chalk);
  }
  .tagline-frame { left: 300px; top: 697px; }
  .tagline { left: 330px; top: 704px; width: 330px; text-align: center; font-size: 30px; line-height: 34px; font-style: italic; }
  .handmade-frame { left: 755px; top: 630px; }
  .handmade { left: 805px; top: 648px; width: 340px; font-size: 29px; line-height: 32px; font-style: italic; }
  .size { left: 445px; top: 836px; font-size: 22px; font-style: italic; }
  .site { left: 420px; top: 876px; font-size: 27px; font-style: italic; color: var(--amber); letter-spacing: 1px; }
</style>
</head>
<body>
<main class="label">

  <p class="abs warning">Warning! To prevent fire and serious injury: Burn candle within sight. Keep away from drafts and vibrations. Keep out of reach of children and pets. Never burn candle on or near anything that can catch fire.</p>

  <svg class="abs guide-arrow" width="24" height="132" viewBox="0 0 24 132" aria-hidden="true">
    <path d="M12 130 L12 6 M2 20 L12 4 L22 20" stroke="var(--chalk-soft)" stroke-width="3" fill="none" stroke-linecap="round"/>
  </svg>

  <h1 class="abs scent-name">Fizzing Mock-ree</h1>
  <svg class="abs scent-underline" width="500" height="20" viewBox="0 0 500 20" aria-hidden="true">
    <path d="M4 15 Q250 8 496 6" stroke="var(--lime)" stroke-width="4" fill="none" stroke-linecap="round"/>
  </svg>

  <section class="abs ingredients">
    <h2>ingredients:</h2>
    <ul>
      <li><svg width="22" height="20" viewBox="0 0 22 20"><path d="M2 10 L8 17 L20 3" stroke="var(--chalk)" stroke-width="2" fill="none"/></svg>natural soy wax</li>
      <li><svg width="22" height="20" viewBox="0 0 22 20"><path d="M2 10 L8 17 L20 3" stroke="var(--chalk)" stroke-width="2" fill="none"/></svg>100%cotton wick</li>
      <li><svg width="22" height="20" viewBox="0 0 22 20"><path d="M2 10 L8 17 L20 3" stroke="var(--chalk)" stroke-width="2" fill="none"/></svg>premium fragrance oil</li>
      <li><svg width="22" height="20" viewBox="0 0 22 20"><path d="M2 10 L8 17 L20 3" stroke="var(--chalk)" stroke-width="2" fill="none"/></svg>passion</li>
      <li><svg width="22" height="20" viewBox="0 0 22 20"><path d="M2 10 L8 17 L20 3" stroke="var(--chalk)" stroke-width="2" fill="none"/></svg>advocacy</li>
    </ul>
  </section>

  <p class="abs discard-note">Discard<br>or<br>Reccycle</p>
  <div class="abs art art-discard" role="img" aria-label="Chalk sketch of a stick figure dropping a bottle into a bin"></div>

  <div class="abs brand-name"><span class="brand-lead">Brim</span><span class="brand-ed">Lo</span></div>

  <p class="abs cause">A portion of the sales go to support <span class="mark">underage</span> drinking prevention programs.</p>
  <div class="abs art art-school" role="img" aria-label="Chalk sketch of a small schoolhouse"></div>

  <p class="abs product-type">Beer Bottle Candles</p>

  <svg class="abs instructions-frame" width="250" height="520" viewBox="0 0 250 520" aria-hidden="true">
    <path d="M14 12 Q120 4 232 8 Q242 10 242 24 L238 492 Q238 508 222 510 Q120 516 22 512 Q8 510 8 494 L10 28 Q10 14 14 12 Z" stroke="var(--amber)" stroke-width="4" fill="none"/>
  </svg>
  <p class="abs instructions">Burning Instructions: Trim wick to 1/4" before each lighting. Keep free from foreign materials including wick trimmings. For an even burn, burn for at least 1 hour but not more than 4 hours at a time. Discontinue use when 1/4" of wax remains.</p>

  <svg class="abs tagline-frame" width="400" height="90" viewBox="0 0 400 90" aria-hidden="true">
    <path d="M6 6 L392 4 M8 6 L10 84 M10 84 L300 86 M14 12 L386 12 M384 6 L386 60" stroke="var(--chalk)" stroke-width="3" fill="none" stroke-linecap="round"/>
  </svg>
  <p class="abs tagline">How Scentsible People<br>Get BrimLo</p>

  <svg class="abs handmade-frame" width="430" height="240" viewBox="0 0 430 240" aria-hidden="true">
    <path d="M60 10 Q220 -2 380 18 Q428 40 420 120 Q412 210 330 228 Q200 240 60 222 Q8 200 8 120 Q10 30 60 10 Z" stroke="var(--chalk-soft)" stroke-width="3" fill="none"/>
  </svg>
  <p class="abs handmade">Handcrafted in the heart of the College Triangle of North Carolina using repurposed beer bottles.</p>
  <div class="abs art art-bottles" role="img" aria-label="Small chalk sketch of three bottles"></div>

  <p class="abs size">11oz. / 311g. /60-80 hours</p>
  <p class="abs site">www.brimlocandles.com</p>

</main>
</body>
</html>
```